PSR Name Badge & Kiosk Stand Wrap

We are needing a name badge, ipad wrape, and stands created. These should be sent in AI, EPS and PDF format. The design guidlaines for the ipad stands are attached. We would like it to match our general overall themeing for Prairie SunRidge. Do not mention a year or location so we can use it for future years.

```html
<!DOCTYPE html>
<html lang="en">
<head>
<meta charset="utf-8">
<title>PSR Name Badge</title>
<link href="https://fonts.googleapis.com/css2?family=Montserrat:wght@600;700&family=Michroma&display=swap" rel="stylesheet">
<style>
  :root {
    --board: #240c16;
    --frame-line: #8a7480;
    --pill: #ffffff;
    --ink: #240c16;
    --paper: #ffffff;
    --sun-yellow: #ffb703;
    --sun-orange: #fb5b05;
    --sun-red: #f5003a;
    --brand-orange: #f77f00;
  }
  * { margin: 0; padding: 0; box-sizing: border-box; }
  html, body { width: 1200px; height: 867px; overflow: hidden; background: var(--board); }
  .board { position: relative; width: 1200px; height: 867px; background: var(--board); }
  .title-pill {
    position: absolute; left: 495px; top: 33px; width: 210px; height: 52px;
    background: var(--pill); border-radius: 16px;
    display: flex; align-items: center; justify-content: center;
    font-family: "Montserrat", sans-serif; font-weight: 700; font-size: 26px; color: var(--ink);
  }
  .divider { position: absolute; left: 600px; top: 133px; width: 1px; height: 734px; background: var(--frame-line); }
  .option-label {
    position: absolute; top: 98px; width: 80px; text-align: center;
    font-family: "Michroma", sans-serif; font-size: 17px; color: #fff; letter-spacing: 1px;
  }
  .option-frame { position: absolute; top: 129px; width: 457px; height: 675px; border: 1px solid var(--frame-line); }
  .badge { position: absolute; left: 10px; top: 10px; width: 436px; height: 655px; overflow: hidden; }
  .badge--light { background: var(--paper); }
  .badge--warm { background: linear-gradient(to bottom, var(--sun-yellow) 0%, var(--sun-orange) 50%, var(--sun-red) 100%); }
  .badge-wave { position: absolute; left: 0; top: 0; }
  .event-mark {
    position: absolute; left: 0; top: 92px; width: 100%;
    display: flex; flex-direction: column; align-items: center; gap: 14px;
  }
  .event-mark__dot { width: 46px; height: 46px; border-radius: 50%; }
  .event-mark__name { font-family: "Montserrat", sans-serif; font-weight: 700; font-size: 30px; }
  .event-mark__sub {
    display: flex; align-items: center; gap: 8px;
    font-family: "Montserrat", sans-serif; font-weight: 600; font-size: 13px; letter-spacing: 1.5px;
  }
  .event-mark__sub::before, .event-mark__sub::after { content: ""; width: 22px; height: 2px; background: currentColor; }
  .badge--light .event-mark__dot { background: var(--sun-yellow); }
  .badge--light .event-mark__name, .badge--light .event-mark__sub { color: var(--brand-orange); }
  .badge--warm .event-mark__dot { background: #fff; }
  .badge--warm .event-mark__name, .badge--warm .event-mark__sub { color: #fff; }
</style>
</head>
<body>
<main class="board">
  <div class="title-pill">Name Badge</div>
  <div class="divider"></div>

  <div class="option-label" style="left:284px">01</div>
  <div class="option-label" style="left:837px">02</div>

  <section class="option-frame" style="left:94px">
    <div class="badge badge--light">
      <div class="event-mark">
        <span class="event-mark__dot"></span>
        <span class="event-mark__name">Prairie SunRidge</span>
        <span class="event-mark__sub">CONFERENCE</span>
      </div>
      <svg class="badge-wave" width="436" height="655" viewBox="0 0 436 655">
        <defs>
          <linearGradient id="waveFill" x1="0" y1="0.2" x2="1" y2="1">
            <stop offset="0" stop-color="#ffb703"/>
            <stop offset="0.5" stop-color="#fb5b05"/>
            <stop offset="1" stop-color="#f5003a"/>
          </linearGradient>
        </defs>
        <path d="M0 534 C40 524 110 525 190 560 C260 590 290 615 360 613 C395 611 420 605 436 598 L436 655 L0 655 Z" fill="url(#waveFill)"/>
      </svg>
    </div>
  </section>

  <section class="option-frame" style="left:649px">
    <div class="badge badge--warm">
      <div class="event-mark">
        <span class="event-mark__dot"></span>
        <span class="event-mark__name">Prairie SunRidge</span>
        <span class="event-mark__sub">CONFERENCE</span>
      </div>
    </div>
  </section>
</main>
</body>
</html>
```